Skin cancer clinic services trifold brochure

Need trifold brochure listing skin cancer services our clinic provides, staff information, location and brief about skin cancer with colours similar to our web site www.Tolvarin.clinic. I will provide more information regarding services and staff but want this colourful and standout as it will be given to other referring doctors or patients

Target Market(s)

Age 40 to 80 years

Industry/Entity Type

Medical

Font styles to use
Serif

Colors

Designer to choose colors to be used in the design.

Requirements
Must have
• Logo, services, contact info, beach or sun look and colours similar to web site or logo

```html
<!DOCTYPE html>
<html lang="en">
<head>
<meta charset="utf-8">
<title>Tolvarin Skin Cancer Clinic – Brochure</title>
<link rel="stylesheet" href="https://fonts.googleapis.com/css2?family=Tinos:wght@400;700&family=Lato:wght@400&display=swap">
<style>
  :root {
    --tan: #e7d2a3;
    --cream: #f8f3e9;
    --white: #ffffff;
    --ink: #1c1a17;
    --sun: #e9962b;
    --sea-deep: #1f5670;
    --sea-mid: #4e8ea3;
    --surf: #b9d3d8;
    --sand-light: #e2c69a;
    --sand-dark: #b48c5f;
  }
  * { margin: 0; padding: 0; box-sizing: border-box; }
  html, body { width: 1200px; height: 848px; overflow: hidden; background: var(--white); }
  .brochure { position: relative; width: 1200px; height: 848px; overflow: hidden; font-family: "Tinos", "Times New Roman", serif; color: var(--ink); }

  .services-panel { position: absolute; left: 0; top: 0; width: 407px; height: 623px; background: var(--cream); }
  .band { position: absolute; left: 0; width: 407px; background: var(--tan); color: var(--white); font-weight: 700; text-transform: uppercase; }
  .band--services { top: 0; height: 70px; padding: 16px 0 0 21px; font-size: 25px; line-height: 22.5px; letter-spacing: 0.3px; }
  .band--contact { top: 623px; height: 42px; padding: 9px 0 0 21px; font-size: 25px; line-height: 25px; letter-spacing: 0.3px; }

  .service-list { position: absolute; left: 21px; top: 91px; width: 342px; list-style: none; }
  .service-list li { position: relative; padding-left: 12px; font-size: 12.4px; line-height: 14.3px; margin-bottom: 14px; }
  .service-list li::before { content: ""; position: absolute; left: 0; top: 3px; width: 6px; height: 6px; background: var(--tan); }
  .service-list strong { font-weight: 700; }

  .contact-panel { position: absolute; left: 0; top: 665px; width: 407px; height: 183px; background: var(--white); }
  .contact-note { position: absolute; left: 21px; top: 5px; font-size: 17px; }
  .contact-lines { position: absolute; left: 21px; top: 27px; font-size: 17px; line-height: 23.3px; }
  .contact-lines .phone { font-size: 22.5px; line-height: 27px; }
  .contact-lines b { font-weight: 700; }

  .name-mark { display: flex; flex-direction: column; align-items: center; font-family: "Tinos", "Times New Roman", serif; color: var(--ink); }
  .name-mark .dot { width: 22px; height: 22px; border-radius: 50%; background: var(--sun); margin-bottom: 5px; }
  .name-mark .word { font-size: 20px; letter-spacing: 2px; line-height: 20px; }
  .name-mark--footer { position: absolute; left: 277px; top: 94px; width: 110px; }

  .beach-photo { position: absolute; left: 407px; top: 0; width: 793px; height: 848px;
    background: linear-gradient(180deg, var(--surf) 0%, var(--sea-deep) 3%, var(--sea-mid) 20%, var(--surf) 31%, var(--sand-light) 38%, #cfae80 65%, var(--sand-dark) 100%); }

  .cover-title { position: absolute; right: 22px; text-align: right; font-weight: 700; }
  .cover-title--main { top: 62px; right: 43px; font-size: 110px; line-height: 108px; color: var(--white); letter-spacing: 2px; }
  .cover-title--sub { top: 173px; font-size: 40px; line-height: 44px; color: var(--ink); letter-spacing: 1.5px; }

  .about-panel { position: absolute; left: 1035px; top: 446px; width: 165px; height: 402px; background: var(--white); }
  .about-panel .cap { height: 43px; background: var(--tan); }
  .name-mark--cover { margin-top: 14px; }
  .name-mark--cover .dot { width: 28px; height: 28px; }
  .name-mark--cover .word { font-size: 22px; }
  .about-text { margin-top: 40px; font-family: "Lato", Arial, sans-serif; font-size: 13.6px; line-height: 18.5px; text-align: center; text-transform: uppercase; color: var(--ink); }
</style>
</head>
<body>
<main class="brochure">
  <section class="services-panel">
    <h2 class="band band--services">Specialised<br>Treatments</h2>
    <ul class="service-list">
      <li><strong>Surgical Procedures –</strong> Our Doctors are proficient in surgical procedures from simple diagnostic biopsies or elliptical excisions to advanced procedures including skin grafts and surgical flap repair, all under a local anaesthetic.</li>
      <li><strong>Radiovex Radiofrequency procedures –</strong> Surgical options include a high frequency radiosurgical device for scalpel-less surgery. It allows our Doctors to use Radiowaves instead of scalpels to provide advanced skin cancer surgical procedures or cosmetic procedures; including removal of spider veins or vascular lesions and benign non-suspicious moles, skin tags, seborrheic keratoses, warts and other raised lesions. A Radiovex procedure ensures minimal thermal tissue damage, bleeding, and recovery time, thus enhancing cosmetic outcome.</li>
      <li><strong>Margin Controlled Surgery (also known as Slow Mohs or Delayed Closure) –</strong> a process where aggressive skin cancers are not closed after excision until the histological status and clearance is known. This can minimise the need for larger excisions and potentially benefit cosmetic outcome; especially in cosmetically sensitive regions such as the nose, ears and face.</li>
      <li><strong>Non-surgical treatments and preventative therapy options –</strong> Our goal is to prevent and treat skin cancer in the least invasive way possible as appropriate. This includes preventative care including Vitamin B3 benefits and sun safe practices - to topical therapies, such as liquid nitrogen and prescriptive therapy for solar keratoses or superficial Non-Melanoma skin cancers.</li>
      <li><strong>Cosmetic Services –</strong> Tolvarin approaches our skin cancer patient holistically and, by appointment, we can offer advice and treatment regarding skin pigmentation, troublesome bumps and lumps and more! Please see our web site at www.tolvarin.clinic for more information.</li>
    </ul>
  </section>

  <h2 class="band band--contact">Contact Us</h2>
  <section class="contact-panel">
    <p class="contact-note">(Please show location map)</p>
    <p class="contact-lines">
      <span class="phone"><b>Phone:</b> 1300 55 0199</span><br>
      <b>Address:</b> Suite 3 &amp; 4, 117 Harbour Road<br>
      Kincumber, NSW 2251<br>
      <b>Fax:</b> &nbsp;4309 2286<br>
      <b>Email:</b> admin@Tolvarin.clinic<br>
      <b>Web site:</b> www.Tolvarin.clinic
    </p>
    <div class="name-mark name-mark--footer"><span class="dot"></span><span class="word">TOLVARIN</span></div>
  </section>

  <div class="beach-photo" role="img" aria-label="Photo of a hand holding a piece of orange coral on a sunlit beach with the sea behind"></div>

  <h1 class="cover-title cover-title--main">SKIN</h1>
  <p class="cover-title cover-title--sub">CANCER CLINIC</p>

  <aside class="about-panel">
    <div class="cap"></div>
    <div class="name-mark name-mark--cover"><span class="dot"></span><span class="word">TOLVARIN</span></div>
    <p class="about-text">Our skilled<br>doctors and<br>nurses have<br>extensive<br>experience<br>and advanced<br>training in skin<br>cancer medicine<br>in order to<br>provide quality<br>care to our<br>patients.</p>
  </aside>
</main>
</body>
</html>
```